Vornel Wellness Business Card

A Double Sided Business Card

I am a private company in Melbourne, Australia, working in the Health industry. I am a nutritionist and lifestyle coach, whom specialises in using raw foods ie. fruits/nuts/vegetables to help heal my clients and enable them to achieve their ultimate state of health.

I want a sophisticated design and colour for my card that appeals to both men and women from teenage through to elderly.

Front of Card:

Red apple peel spiral in the shape of an apple. I would like a leaf/leaves coming off the stem of the apple. Please see attachments for example.

***On Right Hand side of Image is business Name: Vornel Wellness

Underneath LOGO use slogan " Let Food Be Your Medicine"

***Use Deep Red and Blues for Text Colouring

Back of Card:

Marisol Dekkert
Nutritional Specialist and Lifestyle Coach

Specialising in: Diseased Conditions
Weight Management
Achieving your Ultimate State of Health

enquiries@vornelwellness.com.au 0457 396 504

**Make sure the front design of the card flows onto the back.
Updates

Email address has been amended, Also more specific details have been given for apple peel Image, and another image attached as example of Leaf on stem of apple.

I little more insight into what sort of feel were trying to create. We're apart of the health industry, and we want the card to have a medical/clinical feeling about it.

Target Market(s)

Males and Females from teenages to elderly

Industry/Entity Type

Business

Requirements
Must have
• Red Apple Peel Spiral, in the shape of an apple, with a leaf/leaves attached to stem.
***Must be in the shape of an apple
***Please use coloring on inside of apple peel to resemble inside of an apple.
Nice to have
• I would like my card to have a clinical feel.
Should not have
• We don't want the image of the apple to look like a Christmas decoration

```html
<!DOCTYPE html>
<html lang="en">
<head>
<meta charset="utf-8">
<title>Vornel Wellness Business Card</title>
<link href="https://fonts.googleapis.com/css2?family=Quicksand:wght@500;600;700&display=swap" rel="stylesheet">
<style>
  :root {
    --stage: #ecedf0;
    --card-white: #ffffff;
    --card-grey: #d9dadd;
    --swirl-grey: #c9cacd;
    --band-blue: #2f2f86;
    --band-blue-light: #4a4aa8;
    --deep-red: #c8222a;
    --navy-text: #2a2a7a;
    --ink: #1d1d2b;
    --white: #ffffff;
  }
  * { margin: 0; padding: 0; box-sizing: border-box; }
  html, body { width: 1200px; height: 900px; overflow: hidden; }
  body {
    background: var(--stage);
    font-family: "Quicksand", sans-serif;
    position: relative;
  }
  .card {
    position: absolute;
    background: var(--card-white);
    box-shadow: 0 6px 18px rgba(0,0,0,0.22);
    overflow: hidden;
  }
  .card-back { left: 25px; top: 68px; width: 620px; height: 385px; }
  .card-front { left: 545px; top: 458px; width: 600px; height: 385px; }
  .card-art { position: absolute; inset: 0; width: 100%; height: 100%; }

  /* back of card: details */
  .person {
    position: absolute; left: 0; width: 100%;
    text-align: center; top: 134px;
    padding-left: 20px;
  }
  .person-name { color: var(--deep-red); font-size: 29px; font-weight: 500; line-height: 1.1; }
  .person-role { color: var(--white); font-size: 17.5px; font-weight: 600; line-height: 1.1; letter-spacing: 0.3px; }
  .specialties {
    position: absolute; left: 0; width: 100%;
    top: 226px; text-align: center; padding-left: 40px;
    color: var(--ink);
  }
  .specialties-title { color: var(--navy-text); font-size: 19px; font-weight: 600; }
  .specialties-list { font-size: 16px; font-weight: 600; line-height: 1.3; list-style: none; }
  .specialties-list li { display: inline; margin: 0 4px; }
  .specialties-list li::before { content: "·"; margin-right: 2px; }
  .contact {
    position: absolute; left: 42px; top: 318px;
    list-style: none; color: var(--white);
    font-size: 17.5px; font-weight: 500;
  }
  .contact li { display: flex; align-items: center; gap: 9px; height: 26px; }
  .contact-icon { width: 20px; height: 20px; }
  .brand-dot {
    position: absolute; left: 530px; top: 295px;
    width: 46px; height: 46px; border-radius: 50%;
    background: var(--band-blue);
  }

  /* front of card: brand */
  .brand {
    position: absolute; top: 140px; left: 0; width: 100%;
    display: flex; align-items: center; justify-content: center; gap: 16px;
  }
  .brand-mark { width: 54px; height: 54px; border-radius: 50%; background: var(--deep-red); }
  .brand-name { color: var(--deep-red); font-size: 44px; font-weight: 700; letter-spacing: -0.5px; }
  .slogan {
    position: absolute; top: 270px; left: 0; width: 100%;
    text-align: center; color: var(--white);
    font-size: 19px; font-weight: 500;
  }
</style>
</head>
<body>

<section class="card card-back" aria-label="Back of card">
  <svg class="card-art" viewBox="0 0 620 385" preserveAspectRatio="none" aria-hidden="true">
    <defs>
      <linearGradient id="backBg" x1="0" y1="0" x2="0" y2="1">
        <stop offset="0" stop-color="#f6f6f7"/>
        <stop offset="1" stop-color="#e4e5e8"/>
      </linearGradient>
    </defs>
    <rect width="620" height="385" fill="url(#backBg)"/>
    <path d="M0,20 Q320,70 620,20 L620,60 Q320,110 0,60 Z" fill="var(--card-grey)"/>
    <path d="M0,68 Q330,110 620,58 L620,150 Q340,250 0,232 Z" fill="var(--band-blue)"/>
    <path d="M0,232 Q340,250 620,150 L620,175 Q360,270 0,262 Z" fill="#ffffff"/>
    <path d="M150,300 Q400,230 600,250 Q560,300 420,300 Q300,305 150,300 Z" fill="var(--swirl-grey)" opacity="0.6"/>
    <path d="M0,282 Q80,250 240,262 Q120,270 0,302 Z" fill="var(--swirl-grey)" opacity="0.55"/>
    <path d="M0,302 C160,292 380,300 520,385 L0,385 Z" fill="var(--band-blue)"/>
  </svg>

  <div class="person">
    <h1 class="person-name">Marisol Dekkert</h1>
    <p class="person-role">Nutritional Specialist</p>
    <p class="person-role">Lifestyle Coach</p>
  </div>

  <div class="specialties">
    <h2 class="specialties-title">Specialising in:</h2>
    <ul class="specialties-list">
      <li>Diseased Conditions</li>
      <li>Weight Management</li><br>
      <li>Achieving your Ultimate State of Health</li>
    </ul>
  </div>

  <ul class="contact">
    <li>
      <svg class="contact-icon" viewBox="0 0 20 20" aria-hidden="true">
        <circle cx="10" cy="10" r="10" fill="var(--deep-red)"/>
        <circle cx="10" cy="10" r="6" fill="none" stroke="#fff" stroke-width="1.3"/>
        <path d="M4,10 H16 M10,4 V16 M10,4 Q6,10 10,16 M10,4 Q14,10 10,16" fill="none" stroke="#fff" stroke-width="1.1"/>
      </svg>
      enquiries@vornelwellness.com.au
    </li>
    <li>
      <svg class="contact-icon" viewBox="0 0 20 20" aria-hidden="true">
        <circle cx="10" cy="10" r="10" fill="var(--deep-red)"/>
        <path d="M6,5 L8.5,5 L9.5,8 L8,9 Q9,11.5 11,12 L12,10.5 L15,11.5 L15,14 Q9,15 6,5 Z" fill="#fff"/>
      </svg>
      0457 396 504
    </li>
  </ul>

  <div class="brand-dot" aria-hidden="true"></div>
</section>

<section class="card card-front" aria-label="Front of card">
  <svg class="card-art" viewBox="0 0 600 385" preserveAspectRatio="none" aria-hidden="true">
    <defs>
      <linearGradient id="frontBg" x1="0" y1="0" x2="0" y2="1">
        <stop offset="0" stop-color="#f4f4f5"/>
        <stop offset="1" stop-color="#e1e2e5"/>
      </linearGradient>
    </defs>
    <rect width="600" height="385" fill="url(#frontBg)"/>
    <path d="M0,60 Q250,20 600,40 L600,0 L0,0 Z" fill="var(--card-grey)" opacity="0.6"/>
    <path d="M0,200 Q150,150 320,185 Q200,190 0,230 Z" fill="var(--swirl-grey)" opacity="0.7"/>
    <path d="M0,230 Q300,260 600,200 L600,305 Q300,370 0,330 Z" fill="var(--band-blue)"/>
    <path d="M0,330 Q300,370 600,305 L600,330 Q300,395 0,355 Z" fill="#ffffff"/>
    <path d="M60,385 Q300,340 520,385 Z" fill="var(--swirl-grey)" opacity="0.6"/>
  </svg>

  <div class="brand">
    <span class="brand-mark" aria-hidden="true"></span>
    <span class="brand-name">Vornel Wellness</span>
  </div>
  <p class="slogan">Let Food Be Your Medicine</p>
</section>

</body>
</html>
```